Larkfield Ridge Management

I need a professional website. My current website is larkfieldridgemanagement.com and I hate it. It was created with some AI tool very quickly because I needed a site up and running with no advanced notice. I’m open to all designs .. I trust you, the professionals will deliver the results I’m anxiously awaiting! :)

```html
<!DOCTYPE html>
<html lang="en">
<head>
<meta charset="utf-8">
<title>Larkfield Ridge Management</title>
<link rel="stylesheet" href="https://fonts.googleapis.com/css2?family=Poppins:wght@400;500;600;700;800&display=swap">
<style>
:root{
  --navy:#1b2550;
  --red:#c0151f;
  --red-dark:#9e1018;
  --ink:#222;
  --muted:#555;
  --soft:#f4f4f4;
  --white:#fff;
  --black:#070707;
}
*{box-sizing:border-box;margin:0;padding:0}
html,body{width:1200px;height:4971px;overflow:hidden}
body{position:relative;font-family:'Poppins',sans-serif;color:var(--ink);background:var(--white)}
.abs{position:absolute}
.center{left:0;width:1200px;text-align:center}
.title{font-weight:800;color:var(--navy);font-size:46px;letter-spacing:-.5px;line-height:1}
.kicker{color:var(--red);font-weight:600;font-size:20px;display:flex;align-items:center;justify-content:center;gap:12px}
.kicker::before,.kicker::after{content:"";width:40px;height:2px;background:var(--red)}
.btn{display:inline-block;background:var(--red);color:#fff;font-weight:700;font-size:14px;padding:0 30px;height:48px;line-height:48px;clip-path:polygon(8% 0,92% 0,100% 50%,92% 100%,8% 100%,0 50%)}

/* header */
.hero{top:0;left:0;width:1200px;height:760px;background:linear-gradient(180deg,#9fb5c6 0%,#6f8495 40%,#4e6270 65%,#3e6a2c 85%,#2f5a20 100%)}
.contact-chip{display:flex;gap:12px;align-items:center;color:var(--navy)}
.chip-icon{width:36px;height:36px;background:var(--red);clip-path:polygon(50% 0,100% 25%,100% 75%,50% 100%,0 75%,0 25%);display:flex;align-items:center;justify-content:center}
.chip-label{font-size:12px;font-weight:500}
.chip-value{font-size:19px;font-weight:600;line-height:1.1}
.nav{top:93px;left:105px;width:990px;height:82px;background:#fff;clip-path:polygon(4% 0,96% 0,100% 50%,96% 100%,4% 100%,0 50%);box-shadow:0 4px 12px rgba(0,0,0,.1)}
.nav a{position:absolute;top:34px;font-size:14px;font-weight:500;color:#222;text-decoration:none}
.nav a.active{color:var(--red);font-weight:700}
.brand-badge{top:12px;left:490px;width:220px;height:215px;background:#fff;clip-path:polygon(50% 0,100% 22%,100% 75%,50% 100%,0 75%,0 22%);display:flex;flex-direction:column;align-items:center;justify-content:center;gap:8px}
.brand-mark{width:26px;height:26px;background:var(--navy)}
.brand-name{font-weight:700;color:var(--navy);font-size:19px;line-height:1.15;text-align:center}
.hero-h1{top:340px;color:#fff;font-weight:800;font-size:58px;line-height:1;text-shadow:0 3px 8px rgba(0,0,0,.35)}
.hero-h2{top:400px;color:#fff;font-weight:800;font-size:112px;line-height:1;text-shadow:0 3px 8px rgba(0,0,0,.35)}
.hero-sub{top:515px;color:#fff;font-weight:600;font-size:15px;line-height:27px;text-shadow:0 2px 6px rgba(0,0,0,.5)}

/* about */
.about-bg{top:760px;left:0;width:1200px;height:820px;background:linear-gradient(115deg,#f1f1f1 0 30%,#fff 30%)}
.hex-photo{top:1020px;left:122px;width:386px;height:444px;clip-path:polygon(50% 0,100% 25%,100% 75%,50% 100%,0 75%,0 25%);background:linear-gradient(135deg,#c9b7a3,#7d6a58 55%,#3e3a40)}
.about-text{left:598px;top:980px;width:490px}
.about-text p{font-size:14px;line-height:25.7px;color:var(--muted);text-align:justify;margin-bottom:26px}
.sub-split{display:flex;align-items:center;gap:10px;margin:16px 0 22px;font-size:20px;font-weight:600}
.sub-split .a{color:var(--red)}.sub-split .b{color:var(--navy)}
.sub-split i{width:70px;height:2px;background:var(--navy)}

/* services */
.svc{top:1798px;width:280px}
.svc-photo{height:220px}
.svc-band{height:125px;clip-path:polygon(0 0,100% 0,100% 55%,50% 100%,0 55%);text-align:center;color:#fff;font-size:17px;font-weight:500;padding-top:8px}
.svc-icon{width:68px;height:68px;margin:12px auto 0;background:var(--red);clip-path:polygon(50% 0,100% 25%,100% 75%,50% 100%,0 75%,0 25%);display:flex;align-items:center;justify-content:center}
.arrow-btn{top:1927px;width:40px;height:40px;border:2px solid #888;border-radius:50%;display:flex;align-items:center;justify-content:center}

/* why */
.why-bg{top:2245px;left:0;width:1200px;height:745px;background:var(--soft)}
.feat{width:270px}
.feat h4{font-size:15px;font-weight:600;color:#111;margin-bottom:6px}
.feat p{font-size:12.5px;line-height:23px;color:#555}
.feat.left{text-align:right}
.feat-icon{width:48px;height:50px;background:var(--navy);clip-path:polygon(50% 0,100% 25%,100% 75%,50% 100%,0 75%,0 25%);display:flex;align-items:center;justify-content:center}
.why-badge{top:2500px;left:418px;width:364px;height:385px;background:#fff;border:10px solid var(--navy);clip-path:polygon(50% 0,100% 22%,100% 78%,50% 100%,0 78%,0 22%);display:flex;flex-direction:column;align-items:center;justify-content:center;gap:16px}
.why-badge .brand-mark{width:44px;height:44px}
.why-badge .brand-name{font-size:34px}

/* cta */
.cta{top:2990px;left:0;width:1200px;height:490px;background:linear-gradient(135deg,#c81923,#a90f18)}
.cta h2{font-weight:800;color:#fff;font-size:46px;line-height:52px}
.cta .kicker{color:#fff}
.cta .kicker::before,.cta .kicker::after{background:#fff}
.cta p{color:#fff;font-size:14.5px;line-height:26px}
.btn-white{background:#fff;color:var(--red)}

/* proposal */
.field{height:67px;background:#fff;border:1px solid #ddd;display:flex;align-items:center;gap:18px;padding-left:20px;font-size:13px;color:#888}
.field .sep{width:1px;height:26px;background:#ccc}
.skyline{top:4020px;left:0;width:1200px;height:440px;background:linear-gradient(180deg,rgba(220,220,220,0),#e4e4e4 45%,#dcdcdc)}
.submit{top:4140px;left:208px;width:790px;height:52px;background:var(--red);color:#fff;font-weight:700;font-size:14px;text-align:center;line-height:52px;clip-path:polygon(2% 0,98% 0,100% 50%,98% 100%,2% 100%,0 50%)}

/* footer */
.footer{top:4460px;left:0;width:1200px;height:511px;background:var(--black);color:#fff}
.f-head{font-size:21px;font-weight:500}
.f-row{display:flex;gap:16px;align-items:flex-start;font-size:14px;line-height:26px}
.f-ico{width:38px;height:38px;border:2px solid #fff;border-radius:50%;display:flex;align-items:center;justify-content:center;flex:none}
.links li{list-style:none;font-size:14px;display:flex;gap:14px;align-items:center;height:41px}
</style>
</head>
<body>

<!-- HERO -->
<div class="abs hero" role="img" aria-label="Photo of a large grey two-storey family house with white garage doors and a green lawn"></div>
<svg class="abs" style="top:690px;left:0" width="1200" height="190" viewBox="0 0 1200 190">
  <polygon points="0,20 600,150 1200,20 1200,190 0,190" fill="#fff"/>
  <polygon points="0,12 600,132 1200,12 1200,36 600,156 0,36" fill="#1b2550"/>
  <polygon points="0,40 600,160 1200,40 1200,50 600,170 0,50" fill="#fff"/>
</svg>
<div class="abs" style="top:800px;left:567px;width:66px;height:76px;background:#fff;clip-path:polygon(50% 0,100% 22%,100% 78%,50% 100%,0 78%,0 22%);box-shadow:0 0 6px rgba(0,0,0,.2)"></div>
<svg class="abs" style="top:818px;left:581px" width="38" height="38" viewBox="0 0 24 24"><polygon points="12,2 15,9 22,9 16.5,13.5 18.5,21 12,16.5 5.5,21 7.5,13.5 2,9 9,9" fill="#c0151f"/></svg>

<div class="abs contact-chip" style="top:22px;left:110px">
  <div class="chip-icon"><svg width="16" height="16" viewBox="0 0 24 24"><rect x="3" y="6" width="18" height="12" fill="none" stroke="#fff" stroke-width="2"/><path d="M3 6l9 7 9-7" fill="none" stroke="#fff" stroke-width="2"/></svg></div>
  <div><div class="chip-label">Mail Us</div><div class="chip-value">info@larkfieldridge.com</div></div>
</div>
<div class="abs contact-chip" style="top:22px;left:886px">
  <div class="chip-icon"><svg width="16" height="16" viewBox="0 0 24 24"><path d="M6 3l4 4-2 3a11 11 0 006 6l3-2 4 4-3 3C10 21 3 14 3 6z" fill="#fff"/></svg></div>
  <div><div class="chip-label">Call Us</div><div class="chip-value">+1 555 010 2040</div></div>
</div>

<nav class="abs nav">
  <a class="active" style="left:53px">HOME</a>
  <a style="left:140px">ABOUT US</a>
  <a style="left:255px">SERVICES</a>
  <a style="left:628px">REVIEW</a>
  <a style="left:723px">GALLERY</a>
  <a style="left:826px">CONTACT US</a>
</nav>
<div class="abs brand-badge"><div class="brand-mark"></div><div class="brand-name">LARKFIELD<br>RIDGE</div></div>

<h1 class="abs center hero-h1">PROPERTY MANAGEMENT</h1>
<div class="abs center hero-h2">DONE RIGHT.</div>
<p class="abs center hero-sub">Larkfield Ridge Management provides professional, reliable, and<br>stress-free property management services across Ohio.</p>
<div class="abs center" style="top:588px"><span class="btn">GET STARTED</span></div>

<!-- ABOUT -->
<div class="abs about-bg" style="top:880px;height:700px"></div>
<svg class="abs" style="top:985px;left:90px" width="450" height="520" viewBox="0 0 450 520">
  <polygon points="225,6 444,132 444,388 225,514 6,388 6,132" fill="#fff" stroke="#1b2550" stroke-width="12"/>
</svg>
<div class="abs hex-photo" role="img" aria-label="Photo of a smiling family relaxing together on a sofa at home"></div>
<div class="abs about-text">
  <div class="title">ABOUT LARKFIELD</div>
  <div class="sub-split"><span class="a">RIDGE</span><i></i><span class="b">MANAGEMENT</span></div>
  <p>Our organization delivers comprehensive property management solutions that optimize asset performance and tenant satisfaction. By integrating advanced analytics with proven operational frameworks, our specialists ensure each property achieves sustained value appreciation.</p>
  <p>Drawing on decades of collective expertise, the team facilitates regulatory compliance, cost efficiency, and proactive maintenance. This disciplined approach enables owners to preserve capital, enhance occupancy rates, and demonstrate long-term resilience across diverse market conditions. The organization applies rigorously tested frameworks and data-driven methodologies to safeguard property value while elevating tenant experience.</p>
  <span class="btn" style="margin-top:-2px">READ MORE</span>
</div>

<!-- SERVICES -->
<h2 class="abs center title" style="top:1640px">OUR SERVICES</h2>
<div class="abs center kicker" style="top:1695px">WE OFFER</div>
<p class="abs center" style="top:1742px;font-size:14.5px;color:#333">At Larkfield Ridge Management, we believe owning rental property should be rewarding—not stressful.</p>

<div class="abs arrow-btn" style="left:35px"><svg width="18" height="18" viewBox="0 0 24 24"><path d="M20 12H5M11 6l-6 6 6 6" fill="none" stroke="#777" stroke-width="2"/></svg></div>
<div class="abs arrow-btn" style="left:1130px"><svg width="18" height="18" viewBox="0 0 24 24"><path d="M4 12h15M13 6l6 6-6 6" fill="none" stroke="#777" stroke-width="2"/></svg></div>

<div class="abs svc" style="left:132px">
  <div class="svc-photo" role="img" aria-label="Photo of a key with a small house keychain in a door lock" style="background:linear-gradient(135deg,#6b4a33,#a07a58 50%,#3b2a1e)"></div>
  <div class="svc-band" style="background:var(--navy)">Basic Service<div class="svc-icon"><svg width="30" height="30" viewBox="0 0 24 24"><path d="M4 14l4-3h5l2 2-4 1M4 18l5 2 8-3 4-4" fill="none" stroke="#fff" stroke-width="1.6"/></svg></div></div>
</div>
<div class="abs svc" style="left:460px">
  <div class="svc-photo" role="img" aria-label="Photo of a bright modern kitchen and dining room" style="background:linear-gradient(135deg,#e8e8e8,#9a9a9a 55%,#3a3a3a)"></div>
  <div class="svc-band" style="background:var(--red-dark)">Intermediate Service<div class="svc-icon" style="background:var(--navy)"><svg width="30" height="30" viewBox="0 0 24 24"><path d="M4 11l8-6 8 6M6 10v9h12v-9" fill="none" stroke="#fff" stroke-width="1.6"/><circle cx="12" cy="14" r="2.5" fill="none" stroke="#fff" stroke-width="1.6"/></svg></div></div>
</div>
<div class="abs svc" style="left:787px">
  <div class="svc-photo" role="img" aria-label="Photo of a contemporary two-storey white house at dusk" style="background:linear-gradient(180deg,#7aa5d6,#d8d3c6 55%,#4c7a3a)"></div>
  <div class="svc-band" style="background:var(--navy)">Advanced Service<div class="svc-icon"><svg width="30" height="30" viewBox="0 0 24 24"><path d="M4 11l8-6 8 6M6 10v9h12v-9" fill="none" stroke="#fff" stroke-width="1.6"/><circle cx="12" cy="14" r="2.5" fill="none" stroke="#fff" stroke-width="1.6"/></svg></div></div>
</div>

<!-- WHY CHOOSE US -->
<div class="abs why-bg"></div>
<h2 class="abs center title" style="top:2315px">WHY CHOOSE US</h2>
<div class="abs center kicker" style="top:2372px">LARKFIELD</div>
<p class="abs center" style="top:2415px;font-size:14.5px;line-height:29px;color:#333">At Larkfield Ridge Management, we treat your property like our own.<br>Our local expertise, attention to detail, and commitment to exceptional service set us apar</p>

<div class="abs feat left" style="top:2510px;left:60px"><h4>Local Market Expertise</h4><p>We understand Ohio's rental<br>market and help maximize your<br>property's long-term value.</p></div>
<div class="abs feat left" style="top:2656px;left:60px"><h4>Full-Service Management</h4><p>From leasing and maintenance to<br>inspections and reporting, we<br>handle every detail.</p></div>
<div class="abs feat left" style="top:2802px;left:60px"><h4>Qualified Tenant Placement</h4><p>Carefully screened tenants<br>help reduce vacancies and<br>protect your investment.</p></div>
<div class="abs feat-icon" style="top:2518px;left:342px"><svg width="22" height="22" viewBox="0 0 24 24"><rect x="4" y="5" width="16" height="14" fill="none" stroke="#fff" stroke-width="1.8"/><path d="M7 10h10M7 14h6" stroke="#fff" stroke-width="1.8"/></svg></div>
<div class="abs feat-icon" style="top:2664px;left:342px"><svg width="22" height="22" viewBox="0 0 24 24"><circle cx="12" cy="12" r="8" fill="none" stroke="#fff" stroke-width="1.8"/><circle cx="12" cy="10" r="2.5" fill="#fff"/><path d="M7.5 17a5 5 0 019 0" stroke="#fff" stroke-width="1.8" fill="none"/></svg></div>
<div class="abs feat-icon" style="top:2810px;left:342px"><svg width="22" height="22" viewBox="0 0 24 24"><circle cx="12" cy="12" r="8" fill="none" stroke="#fff" stroke-width="1.8"/><path d="M8 12l3 3 5-6" fill="none" stroke="#fff" stroke-width="1.8"/></svg></div>

<div class="abs why-badge"><div class="brand-mark"></div><div class="brand-name">LARKFIELD<br>RIDGE</div></div>

<div class="abs feat-icon" style="top:2518px;left:798px"><svg width="22" height="22" viewBox="0 0 24 24"><circle cx="12" cy="12" r="4" fill="none" stroke="#fff" stroke-width="1.8"/><path d="M12 3v4M12 17v4M3 12h4M17 12h4" stroke="#fff" stroke-width="1.8"/></svg></div>
<div class="abs feat-icon" style="top:2664px;left:798px"><svg width="22" height="22" viewBox="0 0 24 24"><rect x="4" y="4" width="16" height="16" fill="none" stroke="#fff" stroke-width="1.8"/><path d="M8 16v-3M12 16v-6M16 16v-8" stroke="#fff" stroke-width="1.8"/></svg></div>
<div class="abs feat-icon" style="top:2810px;left:798px"><svg width="22" height="22" viewBox="0 0 24 24"><circle cx="12" cy="9" r="3.5" fill="#fff"/><path d="M5 20a7 7 0 0114 0" fill="#fff"/></svg></div>
<div class="abs feat" style="top:2510px;left:865px"><h4>Fast Maintenance Response</h4><p>Trusted vendors and prompt<br>repairs keep your property in<br>excellent condition.</p></div>
<div class="abs feat" style="top:2656px;left:865px"><h4>Transparent Owner Reporting</h4><p>Access detailed financial reports,<br>statements, and updates<br>whenever you need them.</p></div>
<div class="abs feat" style="top:2802px;left:865px"><h4>Dedicated Client Support</h4><p>Our responsive team is here to<br>assist property owners and<br>tenants every step of the way.</p></div>

<!-- CTA -->
<section class="abs cta">
  <h2 class="abs center" style="top:68px">READY TO MAXIMIZE<br>YOUR PROPERTY'S POTENTIAL?</h2>
  <div class="abs center kicker" style="top:180px">CONTACT US</div>
  <p class="abs center" style="top:220px">Let Larkfield Ridge Management handle the day-to-day while you enjoy the returns.<br>Partner with a trusted local team dedicated to protecting your investment. Reliable<br>service, qualified tenants, and transparent reporting—all in one place.</p>
  <div class="abs center" style="top:323px"><span class="btn btn-white">GET A FREE QUOTE</span></div>
</section>
<svg class="abs" style="top:3320px;left:0" width="1200" height="180" viewBox="0 0 1200 180">
  <polygon points="0,40 600,150 1200,40 1200,180 0,180" fill="#fff"/>
  <polygon points="0,20 600,140 1200,20 1200,46 600,166 0,46" fill="#1b2550"/>
</svg>

<!-- PROPOSAL -->
<div class="abs skyline" role="img" aria-label="Light grey city skyline silhouette"></div>
<h2 class="abs center title" style="top:3583px">REQUEST A TAILORED PROPOSAL</h2>
<div class="abs center kicker" style="top:3640px">LARKFIELD</div>
<p class="abs center" style="top:3683px;font-size:14px;line-height:27px;color:#333">Submit the form to initiate a consultative assessment and explore solutions aligned with your<br>objectives. Whether you're a property owner or prospective tenant, our team is here to help.<br>Reach out today and we'll get back to you promptly.</p>

<form>
  <label class="abs field" style="top:3793px;left:210px;width:383px"><svg width="16" height="16" viewBox="0 0 24 24"><circle cx="12" cy="8" r="4" fill="none" stroke="#aaa" stroke-width="1.6"/><path d="M4 21a8 8 0 0116 0" fill="none" stroke="#aaa" stroke-width="1.6"/></svg><span class="sep"></span>First Name</label>
  <label class="abs field" style="top:3793px;left:613px;width:383px"><svg width="16" height="16" viewBox="0 0 24 24"><circle cx="12" cy="8" r="4" fill="none" stroke="#aaa" stroke-width="1.6"/><path d="M4 21a8 8 0 0116 0" fill="none" stroke="#aaa" stroke-width="1.6"/></svg><span class="sep"></span>Last Name</label>
  <label class="abs field" style="top:3880px;left:210px;width:383px"><svg width="16" height="16" viewBox="0 0 24 24"><rect x="3" y="6" width="18" height="12" fill="none" stroke="#aaa" stroke-width="1.6"/><path d="M3 6l9 7 9-7" fill="none" stroke="#aaa" stroke-width="1.6"/></svg><span class="sep"></span>Your Email</label>
  <label class="abs field" style="top:3880px;left:613px;width:383px"><svg width="16" height="16" viewBox="0 0 24 24"><path d="M6 3l4 4-2 3a11 11 0 006 6l3-2 4 4-3 3C10 21 3 14 3 6z" fill="none" stroke="#aaa" stroke-width="1.6"/></svg><span class="sep"></span>Phone Number</label>
  <label class="abs field" style="top:3965px;left:210px;width:786px;height:140px;align-items:flex-start;padding-top:22px"><svg width="16" height="16" viewBox="0 0 24 24"><rect x="4" y="4" width="16" height="16" rx="3" fill="none" stroke="#aaa" stroke-width="1.6"/></svg><span class="sep" style="height:20px"></span>Your Message</label>
  <div class="abs submit">SUBMIT NOW</div>
</form>

<!-- FOOTER -->
<svg class="abs" style="top:4380px;left:0" width="1200" height="90" viewBox="0 0 1200 90">
  <polygon points="0,80 600,0 1200,80 1200,90 0,90" fill="#1b2550"/>
  <polygon points="0,90 600,16 1200,90" fill="#070707"/>
</svg>
<footer class="abs footer">
  <div class="abs f-head" style="top:100px;left:160px">CONTACT US</div>
  <div class="abs f-row" style="top:148px;left:160px"><span class="f-ico"><svg width="16" height="16" viewBox="0 0 24 24"><path d="M12 22s7-7 7-12a7 7 0 00-14 0c0 5 7 12 7 12z" fill="none" stroke="#fff" stroke-width="1.8"/><circle cx="12" cy="10" r="2.5" fill="#fff"/></svg></span><div>Address:<br>Larkfield<br>United States</div></div>
  <div class="abs f-row" style="top:258px;left:160px"><span class="f-ico"><svg width="16" height="16" viewBox="0 0 24 24"><rect x="3" y="6" width="18" height="12" fill="none" stroke="#fff" stroke-width="1.8"/><path d="M3 6l9 7 9-7" fill="none" stroke="#fff" stroke-width="1.8"/></svg></span><div>Email Us:<br>info@larkfieldridge.com</div></div>
  <div class="abs f-row" style="top:344px;left:160px"><span class="f-ico"><svg width="16" height="16" viewBox="0 0 24 24"><path d="M6 3l4 4-2 3a11 11 0 006 6l3-2 4 4-3 3C10 21 3 14 3 6z" fill="#fff"/></svg></span><div>Call Us:<br>+1 555 010 2040</div></div>
  <div class="abs" style="top:90px;left:405px;width:1px;height:330px;background:#444"></div>
  <div class="abs" style="top:90px;left:806px;width:1px;height:330px;background:#444"></div>
  <div class="abs" style="top:140px;left:455px;width:300px;display:flex;flex-direction:column;align-items:center;gap:14px"><div class="brand-mark" style="width:36px;height:36px;background:#fff"></div><div class="brand-name" style="color:#fff;font-size:30px">LARKFIELD<br>RIDGE</div></div>
  <div class="abs f-head" style="top:100px;left:890px">QUICK LINKS</div>
  <ul class="abs links" style="top:142px;left:890px">
    <li><svg width="14" height="14" viewBox="0 0 24 24"><path d="M3 12h15M12 5l7 7-7 7" fill="none" stroke="#fff" stroke-width="3"/></svg>Home</li>
    <li><svg width="14" height="14" viewBox="0 0 24 24"><path d="M3 12h15M12 5l7 7-7 7" fill="none" stroke="#fff" stroke-width="3"/></svg>About</li>
    <li><svg width="14" height="14" viewBox="0 0 24 24"><path d="M3 12h15M12 5l7 7-7 7" fill="none" stroke="#fff" stroke-width="3"/></svg>Services</li>
    <li><svg width="14" height="14" viewBox="0 0 24 24"><path d="M3 12h15M12 5l7 7-7 7" fill="none" stroke="#fff" stroke-width="3"/></svg>Reviews</li>
    <li><svg width="14" height="14" viewBox="0 0 24 24"><path d="M3 12h15M12 5l7 7-7 7" fill="none" stroke="#fff" stroke-width="3"/></svg>Gallery</li>
    <li><svg width="14" height="14" viewBox="0 0 24 24"><path d="M3 12h15M12 5l7 7-7 7" fill="none" stroke="#fff" stroke-width="3"/></svg>Contact Us</li>
  </ul>
  <div class="abs" style="top:432px;left:110px;width:980px;height:1px;background:#555"></div>
  <p class="abs center" style="top:462px;font-size:14px">Copyrights@2026 <b>LARKFIELD</b> All Rights Reserved</p>
</footer>

</body>
</html>
```